Podiatry clinic requires a modern revamp and editing of existing website.

I would like a fresh new look and updated information for my current business website. An easy to navigate site with prominent address and phone number for call to action. We are a podiatry clinic that focuses on general and sports podiatry.
I would like 4 pages; including Home page, About Us, Services & Contact.
www.brambleridgepodiatry.net

Target Market(s)

Active working professionals.

Industry/Entity Type

Medical

Coding

Coded - Design and coding required

Number of Pages Required

4 page

Font styles to use
Sans Serif

Colors
6b449b

Requirements
Must have
• A modern look with logo and active images; clean and uncluttered. Visible phone number and address for call to action.
• 4 pages - Home, About Us, Services, Contact.
• Home page - update address & service logos.
• About Us - update of personal information.
• Services - Revamp of existing page.
• Contact page to include Google map, email & phone number.
Nice to have
• Ability to add content easily; eg. a blog or adding video onto Home page.
• Link to Friendbook page.

```html
<!DOCTYPE html>
<html lang="en">
<head>
<meta charset="utf-8">
<title>Brambleridge Podiatry</title>
<link href="https://fonts.googleapis.com/css2?family=Raleway:wght@400;500;700;800&family=Open+Sans:wght@400;600;700&display=swap" rel="stylesheet">
<style>
:root{
  --purple:#4a2a8e;
  --purple-mid:#5a37a8;
  --purple-soft:#b6a6dd;
  --link:#4b3aa8;
  --green:#6cb52d;
  --ink:#333;
  --muted:#777;
  --grey-bg:#f1f1f1;
  --white:#fff;
}
*{margin:0;padding:0;box-sizing:border-box}
html,body{width:1200px;height:2446px;overflow:hidden}
body{position:relative;font-family:"Open Sans",sans-serif;color:var(--ink);background:var(--white)}
a{color:inherit;text-decoration:none}
h1,h2,h3,h4,h5{font-weight:400}
.abs{position:absolute}

/* top bar */
.topbar{left:0;top:0;width:1200px;height:52px;background:var(--purple);color:var(--white);font-size:21px;display:flex;align-items:center;justify-content:space-between;padding:0 96px}
.topbar span{display:flex;align-items:center;gap:10px}
.sq{width:14px;height:14px;background:var(--white);display:inline-block}

/* header */
.header{left:0;top:52px;width:1200px;height:124px;background:var(--white)}
.logo-disc{left:74px;top:40px;width:200px;height:200px;border-radius:50%;background:var(--white);z-index:3;display:flex;align-items:center;justify-content:center;text-align:center}
.logo-name{font-family:"Raleway",sans-serif;font-weight:700;font-size:30px;line-height:1.1;color:var(--purple)}
.nav{left:410px;top:98px;display:flex;gap:50px;font-family:"Raleway",sans-serif;font-size:18px;color:#555;letter-spacing:.5px}
.nav .active{color:var(--link)}
.call{left:892px;top:86px;display:flex;align-items:center;gap:14px;font-family:"Raleway",sans-serif;font-weight:700;font-size:28px;color:var(--green)}
.call-ico{width:52px;height:52px;border-radius:50%;background:var(--purple);display:flex;align-items:center;justify-content:center}

/* hero */
.hero{left:0;top:176px;width:1200px;height:574px;background:linear-gradient(180deg,#a9c8ea 0%,#dbe4ec 30%,#7ea6b8 40%,#b7b2a8 55%,#8f8a82 100%)}
.hero-title{left:80px;top:305px;font-family:"Raleway",sans-serif;font-weight:800;font-size:46px;line-height:78px;color:var(--purple)}
.hero-text{left:80px;top:455px;width:360px;font-size:21px;line-height:31px;color:#111}
.btn{display:inline-flex;align-items:center;justify-content:center;background:var(--purple);color:var(--white);font-family:"Raleway",sans-serif;font-size:25px;border-radius:32px}
.hero-btn{left:77px;top:573px;width:230px;height:62px}

/* features */
.features{left:0;top:750px;width:1200px;height:374px;background:var(--purple)}
.card{width:323px;color:var(--white)}
.card-img{width:323px;height:206px;border:10px solid var(--purple);background:var(--purple)}
.card-img div{width:100%;height:100%}
.card h3{font-family:"Raleway",sans-serif;font-weight:500;font-size:27px;margin:12px 0 6px 10px}
.card p{font-size:15px;line-height:26px;margin-left:10px;width:300px}
.more{display:block;margin:8px 0 0 10px;font-weight:700;font-size:17px}

/* welcome */
.welcome-img{left:0;top:1124px;width:380px;height:300px;background:linear-gradient(90deg,#f3e3d6,#e7c8b0 60%,#fff)}
.welcome-title{left:0;top:1190px;width:1200px;text-align:center;font-family:"Raleway",sans-serif;font-weight:400;font-size:42px;color:#555}
.welcome-title b{font-weight:400;color:var(--link)}
.welcome-text{left:210px;top:1262px;width:780px;text-align:center;font-size:15px;line-height:25px;color:#555}
.welcome-btn{left:504px;top:1337px;width:191px;height:51px;font-size:23px}

/* news */
.news{left:0;top:1445px;width:1200px;height:500px;background:var(--grey-bg)}
.news-title{left:0;top:1502px;width:1200px;text-align:center;font-family:"Raleway",sans-serif;font-weight:400;font-size:42px;color:#555}
.news-title b{font-weight:400;color:var(--link)}
.post{width:235px;top:1566px}
.post-img{width:235px;height:146px}
.post h4{font-family:"Raleway",sans-serif;font-weight:500;font-size:17px;line-height:25px;color:var(--link);margin-top:12px}
.post time{display:flex;align-items:center;gap:6px;font-size:14px;color:#999;margin:4px 0 6px}
.post p{font-size:15px;line-height:25px;color:#666}

/* partners */
.partners{left:0;top:1945px;width:1200px;height:192px;display:flex;justify-content:space-around;align-items:center;padding:0 60px}
.badge{width:220px;height:70px;border-radius:8px;background:#e4e1ee}

/* footer */
.footer{left:0;top:2137px;width:1200px;height:258px;background:var(--purple)}
.foot-logo{left:82px;top:2190px;font-family:"Raleway",sans-serif;font-weight:700;font-size:32px;line-height:1.2;color:var(--purple-soft)}
.foot-col{top:2172px;color:var(--white)}
.foot-col h5{font-family:"Raleway",sans-serif;font-weight:400;font-size:22px;margin-bottom:14px;color:var(--white)}
.foot-col ul{padding:0}
.foot-col li{list-style:none;display:flex;align-items:flex-start;gap:10px;font-size:17px;line-height:26px;margin-bottom:10px;color:var(--white)}
.foot-col li b{font-weight:700}
.social{display:flex;align-items:center;gap:16px;font-size:18px;margin-bottom:20px;color:var(--white)}
.ring{width:48px;height:48px;border-radius:50%;border:2px solid var(--white);display:inline-block;flex:none}
.copyright{left:0;top:2395px;width:1200px;height:51px;background:var(--purple-mid);color:var(--white);font-size:15px;display:flex;align-items:center;justify-content:center}
</style>
</head>
<body>

<div class="abs topbar">
  <span><svg width="18" height="24" viewBox="0 0 18 24"><path d="M9 0a9 9 0 0 0-9 9c0 7 9 15 9 15s9-8 9-15a9 9 0 0 0-9-9zm0 12.5A3.5 3.5 0 1 1 9 5.5a3.5 3.5 0 0 1 0 7z" fill="#fff"/></svg>Suite 204 / 72 Harrow Lane Eastbrook 3100</span>
  <span><i class="sq"></i>Friendbook</span>
</div>

<header class="abs header"></header>
<div class="abs logo-disc"><span class="logo-name">Brambleridge<br>Podiatry</span></div>
<nav class="abs nav"><a class="active" href="#">HOME</a><a href="#">ABOUT</a><a href="#">SERVICES</a><a href="#">CONTACT</a></nav>
<div class="abs call">
  <span class="call-ico"><svg width="24" height="24" viewBox="0 0 24 24"><path d="M6.6 10.8a15 15 0 0 0 6.6 6.6l2.2-2.2c.3-.3.7-.4 1-.2 1.1.4 2.3.6 3.6.6.6 0 1 .4 1 1V20c0 .6-.4 1-1 1A17 17 0 0 1 3 4c0-.6.4-1 1-1h3.5c.6 0 1 .4 1 1 0 1.3.2 2.5.6 3.6.1.3 0 .7-.2 1z" fill="#fff"/></svg></span>
  1300 555 019
</div>

<section class="abs hero" role="img" aria-label="Photo of bare feet walking along a sandy beach by the sea"></section>
<h1 class="abs hero-title">QUALIFIED HEALTH<br>PROFESSIONALS</h1>
<p class="abs hero-text">Various foot conditions, including Sports Injuries, Orthotic Therapy &amp; Nail Surgery</p>
<a class="abs btn hero-btn" href="#">CONTACT US</a>

<section class="abs features"></section>
<article class="abs card" style="left:78px;top:701px">
  <div class="card-img"><div role="img" aria-label="Photo of a podiatrist in gloves examining a patient's foot" style="background:linear-gradient(135deg,#f4f4f6,#e9d6c8)"></div></div>
  <h3>General Treatment</h3>
  <p>Nails, Corns, Callus, Warts, Skin Disorders, Heel pain / Heel Spurs / Arch pain - plantar Fasciitis</p>
  <a class="more" href="#">READ MORE »</a>
</article>
<article class="abs card" style="left:440px;top:701px">
  <div class="card-img"><div role="img" aria-label="Photo of a nail treatment on a patient's toes" style="background:linear-gradient(135deg,#f7efe9,#edc9b3)"></div></div>
  <h3>Specialised Treatments</h3>
  <p>Diabetic Management, Nail Surgery, Biomechanical Assessment, Gait Analysis, Orthotic Therapy</p>
  <a class="more" href="#">READ MORE »</a>
</article>
<article class="abs card" style="left:802px;top:701px">
  <div class="card-img"><div role="img" aria-label="Video still of a podiatrist in a clinic" style="background:linear-gradient(135deg,#8a97a8,#c9ced6)"></div></div>
  <h3>ABOUT PODIATRISTS</h3>
  <p>Our podiatrists are fully qualified health professionals who are able to diagnose, treat, manage or help to prevent all...</p>
  <a class="more" href="#">READ MORE »</a>
</article>

<div class="abs welcome-img" role="img" aria-label="Photo of a woman's bare legs and feet"></div>
<h2 class="abs welcome-title">WELCOME TO <b>BRAMBLERIDGE PODIATRY</b></h2>
<p class="abs welcome-text">Brambleridge Podiatry is a Podiatry clinic in the heart of Eastbrook centre. We are located between Harrow &amp; Linden Lanes in the Harrow Business Centre / Linden Court Complex.</p>
<a class="abs btn welcome-btn" href="#">READ MORE</a>

<section class="abs news"></section>
<h2 class="abs news-title">LATEST <b>NEWS</b></h2>
<article class="abs post" style="left:78px">
  <div class="post-img" role="img" aria-label="Photo of a physiotherapist stretching a patient's leg" style="background:linear-gradient(135deg,#d9d2c6,#f2efea)"></div>
  <h4>Lorem Ipsum is dummy text and simply printing.</h4>
  <time><svg width="12" height="12" viewBox="0 0 12 12"><rect x="1" y="2" width="10" height="9" fill="none" stroke="#aaa"/><line x1="1" y1="5" x2="11" y2="5" stroke="#aaa"/></svg>01 August 2016</time>
  <p>Lorem Ipsum is simply dummy text of the printing and type setting industry.</p>
</article>
<article class="abs post" style="left:349px">
  <div class="post-img" role="img" aria-label="Photo of feet walking in shallow water" style="background:linear-gradient(180deg,#6f8fa3,#b59c83)"></div>
  <h4>Lorem Ipsum is dummy text and simply printing.</h4>
  <time><svg width="12" height="12" viewBox="0 0 12 12"><rect x="1" y="2" width="10" height="9" fill="none" stroke="#aaa"/><line x1="1" y1="5" x2="11" y2="5" stroke="#aaa"/></svg>01 August 2016</time>
  <p>Lorem Ipsum is simply dummy text of the printing and type setting industry.</p>
</article>
<article class="abs post" style="left:619px">
  <div class="post-img" role="img" aria-label="Illustration of a foot showing heel pain" style="background:linear-gradient(135deg,#fff,#c9b5d8 60%,#e88a7a)"></div>
  <h4>Lorem Ipsum is dummy text and simply printing.</h4>
  <time><svg width="12" height="12" viewBox="0 0 12 12"><rect x="1" y="2" width="10" height="9" fill="none" stroke="#aaa"/><line x1="1" y1="5" x2="11" y2="5" stroke="#aaa"/></svg>01 August 2016</time>
  <p>Lorem Ipsum is simply dummy text of the printing and type setting industry.</p>
</article>
<article class="abs post" style="left:890px">
  <div class="post-img" role="img" aria-label="Photo of a clinician consulting with a patient" style="background:linear-gradient(135deg,#f3ede8,#e2a8a0)"></div>
  <h4>Lorem Ipsum is dummy text and simply printing.</h4>
  <time><svg width="12" height="12" viewBox="0 0 12 12"><rect x="1" y="2" width="10" height="9" fill="none" stroke="#aaa"/><line x1="1" y1="5" x2="11" y2="5" stroke="#aaa"/></svg>01 August 2016</time>
  <p>Lorem Ipsum is simply dummy text of the printing and type setting industry.</p>
</article>

<section class="abs partners" aria-label="Partner memberships">
  <span class="badge"></span><span class="badge"></span><span class="badge"></span><span class="badge"></span>
</section>

<footer class="abs footer"></footer>
<div class="abs foot-logo">Brambleridge<br>Podiatry</div>
<div class="abs foot-col" style="left:350px">
  <h5>Useful Links</h5>
  <ul>
    <li>→ Home</li><li>→ About</li><li>→ Services</li><li>→ Contact</li>
  </ul>
</div>
<div class="abs foot-col" style="left:621px;width:240px">
  <h5>Get In Touch</h5>
  <ul>
    <li><svg width="14" height="20" viewBox="0 0 18 24" style="flex:none;margin-top:3px"><path d="M9 0a9 9 0 0 0-9 9c0 7 9 15 9 15s9-8 9-15a9 9 0 0 0-9-9zm0 12.5A3.5 3.5 0 1 1 9 5.5a3.5 3.5 0 0 1 0 7z" fill="#fff"/></svg><span style="font-size:15px">Suite 204 / 72 Harrow Lane Eastbrook 3100</span></li>
    <li><svg width="16" height="16" viewBox="0 0 24 24" style="flex:none;margin-top:5px"><path d="M6.6 10.8a15 15 0 0 0 6.6 6.6l2.2-2.2c.3-.3.7-.4 1-.2 1.1.4 2.3.6 3.6.6.6 0 1 .4 1 1V20c0 .6-.4 1-1 1A17 17 0 0 1 3 4c0-.6.4-1 1-1h3.5c.6 0 1 .4 1 1 0 1.3.2 2.5.6 3.6.1.3 0 .7-.2 1z" fill="#fff"/></svg><b style="font-size:15px">1300 555 019</b></li>
    <li><svg width="18" height="14" viewBox="0 0 18 14" style="flex:none;margin-top:6px"><rect x="1" y="1" width="16" height="12" fill="none" stroke="#fff" stroke-width="1.5"/><path d="M1 1l8 6 8-6" fill="none" stroke="#fff" stroke-width="1.5"/></svg><span style="font-size:15px">info@brambleridgepodiatry.net</span></li>
  </ul>
</div>
<div class="abs foot-col" style="left:891px">
  <h5>Follow Us</h5>
  <div class="social"><span class="ring"></span>Friendbook</div>
  <div class="social"><span class="ring"></span>Chirper</div>
</div>
<div class="abs copyright">© Brambleridge Podiatry- 2016. All Rights Reserved.</div>

</body>
</html>
```